Maple Roster Business Card for recruitment company

We are looking for a Business Card Design that incorporates our personal details and our busines name and logo. We are a specialized search consultancy that recruit Property and Construction professionals.
We would like a business card that stands out and is appealing to the Construction and Property industry as well.

Target Market(s)

people in the construction and property industry

Contact Information for Business Card

Business Name and logo

Font styles to use
Serif

Colors
0094D4
00A9DD
6FCCEA
C7EBF8
E9F6FB

Requirements
Must have
• Business name and logo as well as contact details
Should not have
• No photos of us please

```html
<!DOCTYPE html>
<html lang="en">
<head>
<meta charset="utf-8">
<title>Maple Roster Business Card</title>
<link rel="stylesheet" href="https://fonts.googleapis.com/css2?family=Jost:wght@300&family=Source+Sans+3:wght@400;700&display=swap">
<style>
  :root {
    --backdrop: #e6e6e7;
    --navy: #03374b;
    --paper: #ececee;
    --ink: #1f2a33;
    --muted-light: #b7c4cc;
  }
  * { box-sizing: border-box; margin: 0; padding: 0; }
  html, body { width: 1200px; height: 1200px; overflow: hidden; }
  body { background: var(--backdrop); position: relative; font-family: "Source Sans 3", sans-serif; }

  .card {
    position: absolute;
    left: 263px;
    width: 683px;
    height: 390px;
    border-radius: 40px;
  }
  .card--front { top: 165px; background: var(--navy); }
  .card--back  { top: 654px; background: var(--paper); }

  .wordmark {
    position: absolute;
    left: 0; right: 0;
    text-align: center;
    font-family: "Jost", sans-serif;
    font-weight: 300;
    letter-spacing: 0.04em;
    line-height: 1;
    white-space: nowrap;
  }
  .card--front .wordmark { top: 158px; font-size: 74px; color: #f2f4f5; }
  .card--back  .wordmark { top: 98px;  font-size: 56px; color: var(--navy); }

  .front-url {
    position: absolute;
    left: 0; right: 0;
    top: 308px;
    text-align: center;
    font-size: 15px;
    letter-spacing: 0.22em;
    color: var(--muted-light);
  }

  .person {
    position: absolute;
    right: calc(683px - 311px);
    top: 227px;
    text-align: right;
    color: var(--ink);
    font-size: 16px;
    line-height: 20px;
  }
  .person__name { font-weight: 700; font-size: 20px; line-height: 24px; color: var(--navy); }

  .divider {
    position: absolute;
    left: 342px;
    top: 235px;
    width: 1.5px;
    height: 52px;
    background: #6b7278;
  }

  .contacts {
    position: absolute;
    left: 375px;
    top: 230px;
    list-style: none;
    color: var(--ink);
    font-size: 16px;
    line-height: 20px;
  }
  .contacts li { display: flex; align-items: center; gap: 10px; }
  .contacts svg { width: 13px; height: 13px; flex: none; }
</style>
</head>
<body>
  <section class="card card--front">
    <div class="wordmark">MAPLE ROSTER</div>
    <div class="front-url">www.mapleroster.nz</div>
  </section>

  <section class="card card--back">
    <div class="wordmark">MAPLE ROSTER</div>

    <div class="person">
      <div class="person__name">Clara Whitfield</div>
      <div>Director</div>
      <div>Senior Search Consultant</div>
    </div>

    <div class="divider"></div>

    <ul class="contacts">
      <li>
        <svg viewBox="0 0 16 16" aria-hidden="true"><path fill="#1f2a33" d="M3.5 1.5l2.5 0 1 3.5-1.6 1.2a9 9 0 0 0 4.4 4.4L11 9l3.5 1v2.5c0 1-1 2-2 2C6.5 14.5 1.5 9.5 1.5 3.5c0-1 1-2 2-2z"/></svg>
        <span>+64 27 000 4821</span>
      </li>
      <li>
        <svg viewBox="0 0 16 16" aria-hidden="true"><rect x="1" y="3" width="14" height="10" fill="#1f2a33"/><path d="M1.5 3.5L8 9l6.5-5.5" stroke="#ececee" stroke-width="1.4" fill="none"/></svg>
        <span>clara@mapleroster.nz</span>
      </li>
      <li>
        <svg viewBox="0 0 16 16" aria-hidden="true"><g fill="none" stroke="#1f2a33" stroke-width="1.4"><circle cx="8" cy="8" r="6.5"/><ellipse cx="8" cy="8" rx="2.8" ry="6.5"/><path d="M1.5 8h13M2.5 4.8h11M2.5 11.2h11"/></g></svg>
        <span>www.mapleroster.nz</span>
      </li>
    </ul>
  </section>
</body>
</html>
```